Yard sign

Looking for a yard sign. <br/>Something simple, name, number. <br/>Large text, readable from 50 feet away. <br/><br/>18 x 24 inches.

Target Market(s)

Potential homeowners thinking about going solar.

Colors

Designer to choose colors to be used in the design.

Requirements
Must have
• "WE'VE GONE SOLAR!"
Nice to have
• We are a solar company, we would like a design that compliments the homeowners decision that they went solar and encourages others to do the same.

```html
<!DOCTYPE html>
<html lang="en">
<head>
<meta charset="utf-8">
<title>Yard Sign – We've Gone Solar</title>
<link href="https://fonts.googleapis.com/css2?family=Montserrat:wght@500;700;800&display=swap" rel="stylesheet">
<style>
  :root {
    --backdrop: #231f20;
    --sign-white: #ffffff;
    --solar-orange: #f4760b;
    --rule-orange: #e05a0a;
    --band-red: #e03205;
    --sun-yellow: #fbb416;
  }
  * { box-sizing: border-box; margin: 0; padding: 0; }
  html, body {
    width: 1200px; height: 1200px; overflow: hidden;
    background: var(--backdrop);
    font-family: 'Montserrat', Arial, sans-serif;
  }
  .yard-sign {
    position: absolute; left: 48px; top: 163px;
    width: 1104px; height: 828px;
    background: var(--sign-white);
  }
  .brand {
    position: absolute; left: 60px; top: 170px;
    display: flex; align-items: center; gap: 22px;
  }
  .brand-dot {
    width: 74px; height: 74px; border-radius: 50%;
    background: var(--sun-yellow); flex: none;
  }
  .brand-name {
    color: var(--solar-orange); font-weight: 800;
    font-size: 50px; line-height: 1; letter-spacing: -0.01em;
    text-transform: uppercase;
  }
  .divider {
    position: absolute; left: 526px; top: 156px;
    width: 3px; height: 212px; border-radius: 2px;
    background: var(--rule-orange);
  }
  .headline {
    position: absolute; left: 566px; color: var(--solar-orange);
    font-weight: 800; line-height: 1; white-space: nowrap;
  }
  .headline-top { top: 166px; font-size: 71px; letter-spacing: 0.005em; }
  .headline-main { top: 228px; font-size: 127px; letter-spacing: -0.01em; }
  .rule { position: absolute; left: 0; width: 100%; background: var(--rule-orange); }
  .rule-top { top: 475px; height: 6px; }
  .rule-bottom { top: 649px; height: 7px; }
  .phone-band {
    position: absolute; left: 0; top: 489px; width: 100%; height: 151px;
    background: var(--band-red);
    display: flex; align-items: center; justify-content: center;
  }
  .phone-number {
    color: var(--sign-white); font-weight: 700; font-size: 136px;
    line-height: 1; letter-spacing: -0.02em; white-space: nowrap;
    padding-top: 4px;
  }
  .rep {
    position: absolute; left: 0; top: 695px; width: 100%; height: 56px;
  }
  .rep-lines { position: absolute; inset: 0; }
  .rep-name {
    position: absolute; left: 0; width: 100%; top: 4px; text-align: center;
    color: var(--rule-orange); font-weight: 500; font-size: 48px;
    line-height: 1; letter-spacing: 0.2em; padding-left: 0.2em;
  }
</style>
</head>
<body>
  <main class="yard-sign">
    <div class="brand">
      <span class="brand-dot"></span>
      <span class="brand-name">Brightside<br>Energy</span>
    </div>
    <div class="divider"></div>
    <h1>
      <span class="headline headline-top">WE’VE GONE</span>
      <span class="headline headline-main">SOLAR!</span>
    </h1>
    <div class="rule rule-top"></div>
    <div class="phone-band"><p class="phone-number">123 456 7890</p></div>
    <div class="rule rule-bottom"></div>
    <div class="rep">
      <svg class="rep-lines" width="1104" height="56" viewBox="0 0 1104 56">
        <polygon points="120,28 275,25 275,31" fill="#e05a0a"/>
        <polygon points="839,25 1022,28 839,31" fill="#e05a0a"/>
      </svg>
      <p class="rep-name">JONATHAN DOE</p>
    </div>
  </main>
</body>
</html>
```